Etiketten-Design für Kräuterbonbon-Metalldose
Katrin Wolber hat sehr viel Talent. Das Design ist absolut kreativ.
Zielgruppe
Unsere Firma FelvoNat verkauft verschiedene Sorten Kräuterbonbons.
Wir brauchen ein Etikett, dass auf eine Metall-Dose (Durchmesser 10 cam, Höhe ca. 3 cm) geklebt wird.
Zielgruppe: jung-alt
Aufgabenstellung
Der Name unserer Kräuterbonbons ist Moospille.
Wir möchten, dass unsere Kunden, wenn sie das Etikett sehen einen Bezug zur Schweiz herstellen können.
Wir verwenden für unsere Bonbons unterschiedliche Kräuter für verschiedene Anwendungen:
Konkret sind erstmal 4 Dosen geplant:
-Kräutermischung aus 16 Kräuter gegen Husten
-Salbei gegen Halsschmerzen
-Anis gegen Magenschmerzen
-Zitrone/Ingwer für die Nerven
Vorderseite: Produktbeschreibung
Rückseite: unsere Herstellerangaben
Größenangaben der Dose: Durchmesser 10 cm, Höhe ca. 3 cm
Im Anhang habe ich Ihnen noch weitere/ genauere Informationen zur Verfügung bereitgestellt!

```html
<!DOCTYPE html>
<html lang="de">
<head>
<meta charset="utf-8">
<title>Moospille – Dosenetiketten</title>
<link rel="stylesheet" href="https://fonts.googleapis.com/css2?family=Caveat+Brush&family=Montserrat:wght@600&display=swap">
<style>
  :root {
    --paper: #ffffff;
    --gold: #bf9a2e;
    --brand-red: #e30613;
    --ink: #111111;
    --sage: #6fbf8f;
    --sage-soft: #d9ecdf;
    --anise: #2a9aa3;
    --anise-soft: #cfe0e5;
    --ginger: #fdd45a;
    --ginger-soft: #fdf0c8;
  }
  html, body {
    margin: 0;
    padding: 0;
    width: 1200px;
    height: 2678px;
    overflow: hidden;
    background: var(--paper);
  }
  .sheet { display: block; width: 1200px; height: 2678px; }
  .wordmark {
    font-family: "Caveat Brush", cursive;
    font-size: 64px;
    letter-spacing: 3px;
    text-transform: uppercase;
  }
  .wordmark--master { fill: var(--ink); font-size: 72px; }
  .wordmark--label { fill: var(--brand-red); }
  .tagline {
    font-family: "Montserrat", sans-serif;
    font-weight: 600;
    font-size: 22px;
    fill: var(--brand-red);
    letter-spacing: 0.5px;
  }
  .variety, .indication {
    font-family: "Caveat Brush", cursive;
    text-transform: uppercase;
  }
  .variety { font-size: 124px; letter-spacing: 6px; }
  .indication { font-size: 46px; letter-spacing: 4px; }
  .label-ring { fill: var(--paper); stroke: var(--gold); stroke-width: 27; }
  .label--sage .variety, .label--sage .indication { fill: var(--sage); }
  .label--anise .variety, .label--anise .indication { fill: var(--anise); }
  .label--ginger .variety, .label--ginger .indication { fill: var(--ginger); }
  .label--ginger .variety { font-size: 118px; letter-spacing: 4px; }
  .herb--sage { fill: var(--sage-soft); }
  .herb--anise { fill: var(--anise-soft); }
  .herb--ginger { fill: var(--ginger-soft); }
</style>
</head>
<body>
<svg class="sheet" viewBox="0 0 1200 2678" xmlns="http://www.w3.org/2000/svg">
  <defs>
    <!-- Salbei -->
    <path id="sage-indication" d="M772 961 A255 255 0 0 0 533 546"/>
    <path id="sage-variety" d="M342 883 A250 250 0 0 0 812 883"/>
    <path id="sage-tagline" d="M397 807 A190 190 0 0 1 658 624"/>
    <!-- Anis -->
    <path id="anise-indication" d="M757 1693 A255 255 0 0 0 533 1244"/>
    <path id="anise-variety" d="M342 1581 A250 250 0 0 0 812 1581"/>
    <path id="anise-tagline" d="M397 1505 A190 190 0 0 1 658 1322"/>
    <!-- Ingwer-Zitrone -->
    <path id="ginger-variety" d="M319 2238 A262 262 0 1 0 745 1992"/>
    <path id="ginger-indication" d="M757 2013 A255 255 0 0 0 346 2085"/>
    <path id="ginger-tagline" d="M397 2203 A190 190 0 0 1 658 2020"/>
  </defs>

  <!-- Master-Wortmarke -->
  <g class="brand-master">
    <text class="wordmark wordmark--master" x="577" y="230" text-anchor="middle">Moospille</text>
  </g>

  <!-- Etikett Salbei -->
  <g class="label label--sage">
    <circle class="label-ring" cx="577" cy="797" r="300"/>
    <path class="herb herb--sage" role="img" aria-label="Zarte Illustration von Salbeiblättern"
      d="M335 800 C380 830 420 880 480 905 C450 930 400 950 355 965 C320 930 305 860 335 800 Z"/>
    <text class="tagline"><textPath href="#sage-tagline">TRADITIONAL SWISS FORMULA</textPath></text>
    <text class="wordmark wordmark--label" x="590" y="822" text-anchor="middle">Moospille</text>
    <text class="indication"><textPath href="#sage-indication">Bei Halsschmerzen</textPath></text>
    <text class="variety"><textPath href="#sage-variety" startOffset="50%" text-anchor="middle">Salbei</textPath></text>
  </g>

  <!-- Etikett Anis -->
  <g class="label label--anise">
    <circle class="label-ring" cx="577" cy="1495" r="300"/>
    <path class="herb herb--anise" role="img" aria-label="Zarte Illustration eines Sternanis"
      d="M405 1525 L460 1560 L490 1615 L440 1640 L430 1700 L395 1660 L340 1665 L360 1615 L325 1580 L380 1570 Z"/>
    <text class="tagline"><textPath href="#anise-tagline">TRADITIONAL SWISS FORMULA</textPath></text>
    <text class="wordmark wordmark--label" x="590" y="1520" text-anchor="middle">Moospille</text>
    <text class="indication"><textPath href="#anise-indication">Bei Magenschmerzen</textPath></text>
    <text class="variety"><textPath href="#anise-variety" startOffset="50%" text-anchor="middle">Anis</textPath></text>
  </g>

  <!-- Etikett Ingwer-Zitrone -->
  <g class="label label--ginger">
    <circle class="label-ring" cx="577" cy="2193" r="300"/>
    <path class="herb herb--ginger" role="img" aria-label="Zarte Illustration von Ingwerwurzel und Zitronenscheibe"
      d="M345 2085 C375 2080 390 2120 380 2160 C400 2200 400 2255 370 2280 C335 2300 305 2260 315 2220 C320 2180 320 2120 345 2085 Z"/>
    <text class="tagline"><textPath href="#ginger-tagline">TRADITIONAL SWISS FORMULA</textPath></text>
    <text class="wordmark wordmark--label" x="590" y="2218" text-anchor="middle">Moospille</text>
    <text class="indication"><textPath href="#ginger-indication" startOffset="50%" text-anchor="middle">Für die Nerven</textPath></text>
    <text class="variety"><textPath href="#ginger-variety">Ingwer-Zitrone</textPath></text>
  </g>
</svg>
</body>
</html>
```